Landing page design for my current website

I need a landing page designed for my Wordpress website. My website is Velmorquay.com, and I need a page that will serve as a landing page for online ads I run. Please follow the color scheme of the current website

This web page will be targeted towards real estate owners who are looking for a property manager. Above the fold needs to have a CTA form headlined with "As a Rental Property Owner, I Want More Protection, Less Stress, and Drama-Free Living"

A few highlights that can be listed beyond the CTA and fold

- Comprehensive Property Management
Full-service management covering tenant placement, leasing, maintenance, and inspections.

Maximized Rental Income
Proven strategies to optimize rental rates and minimize vacancies, ensuring higher ROI.

Stress-Free Management
We handle all tenant interactions, maintenance requests, and property issues, so you don't have to.

Experienced Team
Over a decade of experience in managing single-family homes, small multifamily units, and apartment complexes.

Advanced Technology
Utilize cutting-edge property management software for efficient communication, rent collection, and maintenance tracking.

Tenant Screening and Placement
Thorough background checks and tenant screening processes to ensure reliable and responsible tenants.

Regular Property Inspections
Routine inspections to maintain property condition and address issues before they become costly problems.

Legal Compliance
Expertise in local and federal rental laws to keep your properties compliant and avoid legal hassles.

Transparent Reporting
Detailed monthly reports and financial statements to keep you informed about your property's performance.

Personalized Service
Tailored management plans to meet the unique needs of your properties and investment goals.
Effective Tenant Conflict Resolution
Skilled in handling challenging tenant situations, ensuring conflicts are resolved quickly and professionally to maintain a peaceful living environment and protect your investment.

```html
<!DOCTYPE html>
<html lang="en">
<head>
<meta charset="utf-8">
<title>Velmorquay Realty – Property Owner Landing Page</title>
<link href="https://fonts.googleapis.com/css2?family=Poppins:wght@500;600;700&family=Roboto:wght@400;500;700&display=swap" rel="stylesheet">
<style>
  :root{
    --navy:#163f73;
    --sky:#1f8fcf;
    --ink:#2b2b2b;
    --muted:#9a9a9a;
    --line:#e6e6e6;
    --white:#ffffff;
    --black:#000000;
  }
  *{box-sizing:border-box;margin:0;padding:0}
  html,body{width:1200px;height:3008px;overflow:hidden;background:var(--white)}
  body{position:relative;font-family:'Roboto',sans-serif;color:var(--ink)}
  .abs{position:absolute}

  /* header */
  .brand{left:111px;top:24px;display:flex;align-items:center;gap:10px}
  .brand-mark{width:46px;height:46px;border-radius:50%;border:3px solid var(--navy)}
  .brand-name{font-family:'Poppins',sans-serif;font-weight:600;font-size:22px;color:var(--navy);line-height:1}
  .login{left:896px;top:21px;width:125px;height:52px;border:2px solid var(--navy);border-radius:26px;display:flex;align-items:center;justify-content:center;gap:8px;font-family:'Poppins',sans-serif;font-weight:600;font-size:15px;color:var(--navy)}
  .menu{left:1042px;top:25px;width:44px;height:44px;border-radius:50%;background:var(--navy);display:flex;flex-direction:column;align-items:center;justify-content:center;gap:5px}
  .menu span{width:20px;height:2px;background:var(--white)}
  .divider{left:111px;top:95px;width:977px;height:1px;background:var(--line)}

  /* hero */
  .headline{left:0;top:140px;width:1200px;text-align:center;font-family:'Poppins',sans-serif;font-weight:600;font-size:32px;line-height:52px;color:var(--ink)}
  .headline em{font-style:normal;color:var(--sky)}
  .hero-photo{left:0;top:290px;width:1200px;height:439px;background:linear-gradient(180deg,#dfe6ea 0%,#c9bfae 45%,#8f8a80 80%,#6d6b68 100%)}
  .lead-form{left:237px;top:268px;width:726px;height:277px;background:var(--white);border:1px solid var(--line);border-radius:6px}
  .field{position:absolute;width:298px;height:54px;border:1px solid var(--line);border-radius:27px;padding-left:19px;display:flex;align-items:center;font-size:12px;color:var(--muted)}
  .submit{position:absolute;left:296px;top:183px;width:133px;height:52px;border-radius:26px;background:var(--sky);color:var(--white);font-family:'Poppins',sans-serif;font-weight:600;font-size:16px;display:flex;align-items:center;justify-content:center}

  /* highlights */
  .section-title{left:0;top:795px;width:1200px;text-align:center;font-family:'Poppins',sans-serif;font-weight:500;font-size:35px;color:var(--ink)}
  .feature h3{font-family:'Poppins',sans-serif;font-weight:500;font-size:26px;line-height:41px;color:var(--ink)}
  .feature p{margin-top:18px;font-size:18px;line-height:29px;color:var(--ink)}
  .btn{display:inline-flex;margin-top:28px;width:150px;height:53px;border-radius:27px;background:var(--sky);color:var(--white);font-family:'Roboto',sans-serif;font-weight:700;font-size:17px;align-items:center;justify-content:center}
  .feature-photo{width:300px;height:300px;border-radius:50%}

  /* pagination */
  .pager{left:379px;top:2507px;display:flex;border:1px solid var(--line);border-radius:3px}
  .pager span{width:52px;height:43px;display:flex;align-items:center;justify-content:center;border-right:1px solid var(--line);font-size:15px;color:var(--navy)}
  .pager span:first-child,.pager span:last-child{width:64px}
  .pager span:last-child{border-right:none}
  .pager .current{background:#e9eef2}

  /* footer */
  .footer{left:0;top:2632px;width:1200px;height:376px;background:var(--black);border-top:6px solid var(--navy);border-radius:60px 60px 0 0;color:var(--white)}
  .foot-brand{left:118px;top:120px;display:flex;align-items:center;gap:8px}
  .foot-brand .brand-mark{width:38px;height:38px;border-color:var(--white)}
  .foot-brand .brand-name{color:var(--white);font-size:18px}
  .social{top:182px;width:38px;height:38px;border-radius:50%;background:var(--white)}
  .foot-sep{left:390px;top:80px;width:1px;height:180px;background:#333}
  .foot-col h4{font-family:'Poppins',sans-serif;font-weight:600;font-size:20px;margin-bottom:14px}
  .foot-col li{list-style:none;font-size:15px;line-height:26px;display:flex;gap:10px}
  .foot-col li::before{content:"»";font-size:16px}
  .contact li{list-style:none;font-size:15px;line-height:26px;display:flex;gap:10px;margin-bottom:14px}
  .contact li::before{content:none}
  .contact svg{flex:none;margin-top:5px}
  .foot-rule{left:111px;top:285px;width:977px;height:1px;background:#2a2a2a}
  .copyright{left:0;top:322px;width:1200px;text-align:center;font-size:15px}
</style>
</head>
<body>

<header>
  <div class="abs brand">
    <div class="brand-mark"></div>
    <div class="brand-name">VELMORQUAY REALTY</div>
  </div>
  <div class="abs login">
    <svg width="12" height="13" viewBox="0 0 12 13"><circle cx="6" cy="3.5" r="3" fill="#163f73"/><path d="M0 13c0-4 2.5-5.5 6-5.5S12 9 12 13z" fill="#163f73"/></svg>
    LOG IN
  </div>
  <div class="abs menu"><span></span><span></span><span></span></div>
  <div class="abs divider"></div>
</header>

<section>
  <h1 class="abs headline">As a Rental Property Owner, <em>I Want More Protection</em>,<br><em>Less Stress</em>, and Drama-Free Living</h1>
  <div class="abs hero-photo" role="img" aria-label="Row of suburban rental houses along a curved street"></div>
  <form class="abs lead-form">
    <div class="field" style="left:54px;top:26px">Name</div>
    <div class="field" style="left:373px;top:26px">Email</div>
    <div class="field" style="left:54px;top:103px">Phone</div>
    <div class="field" style="left:373px;top:103px">Address</div>
    <div class="submit">SUBMIT</div>
  </form>
</section>

<section>
  <h2 class="abs section-title">Our Highlights</h2>

  <div class="abs feature" style="left:111px;top:943px;width:460px">
    <h3>Comprehensive Property<br>Management</h3>
    <p>Full-service management covering tenant placement, leasing, maintenance, and inspections.</p>
    <span class="btn">LEARN MORE</span>
  </div>
  <div class="abs feature-photo" style="left:705px;top:918px;background:linear-gradient(135deg,#1c2f5a 0%,#c9b9a6 50%,#e9e7e3 100%)" role="img" aria-label="Handshake over a desk with small model houses"></div>

  <div class="abs feature-photo" style="left:161px;top:1311px;background:radial-gradient(circle at 45% 55%,#c9a57a 0%,#6b4e30 50%,#111 100%)" role="img" aria-label="Model house beside stacks of coins"></div>
  <div class="abs feature" style="left:649px;top:1352px;width:410px">
    <h3>Maximized Rental Income</h3>
    <p>Proven strategies to optimize rental rates and minimize vacancies, ensuring higher ROI.</p>
    <span class="btn">LEARN MORE</span>
  </div>

  <div class="abs feature" style="left:111px;top:1738px;width:430px">
    <h3>Stress-Free Management</h3>
    <p>We handle all tenant interactions, maintenance requests, and property issues, so you don't have to.</p>
    <span class="btn">LEARN MORE</span>
  </div>
  <div class="abs feature-photo" style="left:705px;top:1695px;background:linear-gradient(135deg,#3d5f86 0%,#d8c8b2 50%,#8ca3b8 100%)" role="img" aria-label="Relaxed professional leaning back at an office desk"></div>

  <div class="abs feature-photo" style="left:161px;top:2088px;background:linear-gradient(135deg,#2a2a2a 0%,#b7a58d 50%,#d9dde0 100%)" role="img" aria-label="Team of three colleagues talking in a modern office"></div>
  <div class="abs feature" style="left:648px;top:2119px;width:410px">
    <h3>Experienced Team</h3>
    <p>Over a decade of experience in managing single-family homes, small multifamily units, and apartment complexes.</p>
    <span class="btn">LEARN MORE</span>
  </div>

  <nav class="abs pager">
    <span><svg width="10" height="14" viewBox="0 0 10 14"><path d="M8 1 2 7l6 6" fill="none" stroke="#163f73" stroke-width="2"/></svg></span>
    <span>1</span><span class="current">2</span><span>3</span><span>4</span><span>5</span><span>6</span>
    <span><svg width="10" height="14" viewBox="0 0 10 14"><path d="M2 1l6 6-6 6" fill="none" stroke="#163f73" stroke-width="2"/></svg></span>
  </nav>
</section>

<footer class="abs footer">
  <div class="abs foot-brand">
    <div class="brand-mark"></div>
    <div class="brand-name">VELMORQUAY REALTY</div>
  </div>
  <div class="abs social" style="left:111px"></div>
  <div class="abs social" style="left:163px"></div>
  <div class="abs foot-sep"></div>

  <div class="abs foot-col" style="left:432px;top:76px">
    <h4>Navigation</h4>
    <ul><li>Home</li><li>For Investors</li><li>Residents</li><li>Contact</li><li></li></ul>
  </div>
  <div class="abs foot-col" style="left:640px;top:76px">
    <h4>About Brightfield</h4>
    <ul><li>Fenmoor</li><li>Ashcombe</li><li>Larkridge</li><li>Thornvale</li></ul>
  </div>
  <div class="abs foot-col contact" style="left:864px;top:76px">
    <h4>Contact us</h4>
    <ul>
      <li><svg width="12" height="17" viewBox="0 0 12 17"><path d="M6 0a6 6 0 0 0-6 6c0 4.5 6 11 6 11s6-6.5 6-11a6 6 0 0 0-6-6z" fill="#fff"/><circle cx="6" cy="6" r="2.2" fill="#000"/></svg><span>48 Harlow Lane,<br>Fenmoor PA, 17290</span></li>
      <li><svg width="16" height="16" viewBox="0 0 16 16"><path d="M3 0l3 4-2 2c1 2.5 3.5 5 6 6l2-2 4 3-2 3C7 16 0 9 0 2z" fill="#fff"/></svg><span>555.014.2286</span></li>
      <li><svg width="17" height="13" viewBox="0 0 17 13"><rect width="17" height="13" rx="1.5" fill="#fff"/><path d="M1 1.5l7.5 6 7.5-6" fill="none" stroke="#000" stroke-width="1.4"/></svg><span>hello@Velmorquay.com</span></li>
    </ul>
  </div>

  <div class="abs foot-rule"></div>
  <p class="abs copyright">©Copyrights 2024 Velmorquay &nbsp;| &nbsp; All Rights Reserved</p>
</footer>

</body>
</html>
```